4th Generation Family Business Needs a New Card Design!

We are a family owned 4th Generation company. We are based in the Sydney, Australia area and we are desperately in need of a more modern and classy card. We are monumental masons who design, supply & erect lasting memorials throughout cemeteries in Sydney. Our customers are normally in a period of grieving. I have attached logo files that will need to be implemented on the card. Company was established 1935. Australian Owned and Operated. Card needs to be designed to PIXO.com specification.

Target Market(s)

Our target market is based upon people that a grieving for family members that have passed away. We also deal with alot of companies that own and operate cemeteries.

Industry/Entity Type

Business

Contact Information for Business Card

Simon Harcourt, Operations Manager, 0417293086, simon@harcourtmemorials.com.au
Lewis Harcourt, Director, 0491630572, lewis@harcourtmemorials.com.au
Phone # 02 9561 3048
Website: www.harcourtmemorials.com.au
Address: Suite 17, 8 Palfrey Lane, West Carlow, Sydney NSW 2156

Font styles to use
Serif
Decorative
Script

Requirements
Must have
• Would like to see the logo nicely implemented with a modern design. Embossed lettering would be a nice additive.

```html
<!DOCTYPE html>
<html lang="en">
<head>
<meta charset="utf-8">
<title>Harcourt Memorials — Business Card</title>
<link rel="stylesheet" href="https://fonts.googleapis.com/css2?family=Open+Sans:wght@400;600;700&display=swap">
<style>
  :root {
    --backdrop: #e9e6e1;
    --card-white: #ffffff;
    --card-dark: #232223;
    --gold: #ecbd2c;
    --ink: #1e1d1d;
    --paper-text: #ffffff;
  }
  * { box-sizing: border-box; margin: 0; padding: 0; }
  html, body {
    width: 1200px; height: 900px; overflow: hidden;
    background: var(--backdrop);
    font-family: "Open Sans", Arial, sans-serif;
  }
  .stage {
    width: 1200px; height: 900px;
    display: flex; align-items: center; justify-content: center; gap: 40px;
  }
  .card {
    width: 540px; height: 330px; position: relative; overflow: hidden;
    box-shadow: 0 6px 18px rgba(0,0,0,.18);
  }
  /* Front */
  .card-front { background: var(--card-white); }
  .front-brand {
    height: 205px; display: flex; align-items: center; justify-content: center; gap: 14px;
  }
  .brand-mark { width: 26px; height: 26px; background: var(--ink); }
  .brand-name {
    font-size: 34px; font-weight: 600; color: var(--ink); letter-spacing: .5px;
  }
  .front-band {
    position: absolute; left: 0; right: 0; bottom: 0; height: 125px;
    background: var(--gold); color: var(--paper-text);
    display: flex; flex-direction: column; justify-content: center; align-items: center;
    font-size: 14px; font-weight: 600; line-height: 1.9;
  }
  .front-band .divider { margin: 0 12px; font-weight: 400; }
  /* Back */
  .card-back { background: var(--card-dark); color: var(--paper-text); }
  .contacts { position: absolute; left: 52px; top: 52px; }
  .contact + .contact { margin-top: 26px; }
  .contact-name { color: var(--gold); font-weight: 700; font-size: 18px; line-height: 1.3; }
  .contact-role { font-size: 15px; margin-bottom: 6px; }
  .contact-line { display: flex; align-items: center; gap: 8px; font-size: 15px; line-height: 1.45; }
  .contact-line svg { width: 12px; height: 12px; fill: var(--gold); flex: none; }
  .back-brand {
    position: absolute; right: 36px; top: 60px; width: 170px;
    display: flex; flex-direction: column; align-items: center; gap: 10px;
  }
  .back-brand .brand-mark { background: var(--gold); width: 30px; height: 30px; }
  .back-brand .brand-name { color: var(--paper-text); font-size: 20px; text-align: center; line-height: 1.2; }
</style>
</head>
<body>
<main class="stage">
  <section class="card card-front" aria-label="Card front">
    <div class="front-brand">
      <span class="brand-mark"></span>
      <span class="brand-name">Harcourt Memorials</span>
    </div>
    <div class="front-band">
      <p>P: 02 9561 3048<span class="divider">|</span>www.harcourtmemorials.com.au</p>
      <p>Suite 17, 8 Palfrey Lane, West Carlow, Sydney NSW 2156</p>
    </div>
  </section>

  <section class="card card-back" aria-label="Card back">
    <div class="contacts">
      <div class="contact">
        <p class="contact-name">Simon Harcourt</p>
        <p class="contact-role">Operations Manager</p>
        <p class="contact-line"><svg viewBox="0 0 24 24"><path d="M6.6 10.8a15.1 15.1 0 0 0 6.6 6.6l2.2-2.2a1 1 0 0 1 1-.25 11.4 11.4 0 0 0 3.6.57 1 1 0 0 1 1 1V20a1 1 0 0 1-1 1A17 17 0 0 1 3 4a1 1 0 0 1 1-1h3.5a1 1 0 0 1 1 1c0 1.25.2 2.45.57 3.57a1 1 0 0 1-.25 1z"/></svg>0417293086</p>
        <p class="contact-line"><svg viewBox="0 0 24 24"><path d="M2 5h20v14H2z M2 5l10 8 10-8" fill-rule="evenodd"/></svg>simon@harcourtmemorials.com.au</p>
      </div>
      <div class="contact">
        <p class="contact-name">Lewis Harcourt</p>
        <p class="contact-role">Director</p>
        <p class="contact-line"><svg viewBox="0 0 24 24"><path d="M6.6 10.8a15.1 15.1 0 0 0 6.6 6.6l2.2-2.2a1 1 0 0 1 1-.25 11.4 11.4 0 0 0 3.6.57 1 1 0 0 1 1 1V20a1 1 0 0 1-1 1A17 17 0 0 1 3 4a1 1 0 0 1 1-1h3.5a1 1 0 0 1 1 1c0 1.25.2 2.45.57 3.57a1 1 0 0 1-.25 1z"/></svg>0491630572</p>
        <p class="contact-line"><svg viewBox="0 0 24 24"><path d="M2 5h20v14H2z M2 5l10 8 10-8" fill-rule="evenodd"/></svg>lewis@harcourtmemorials.com.au</p>
      </div>
    </div>
    <div class="back-brand">
      <span class="brand-mark"></span>
      <span class="brand-name">Harcourt Memorials</span>
    </div>
  </section>
</main>
</body>
</html>
```